Income Tax Flyer - Updates Needed

Just need to update this flyer design and give it a new look. We would like to keep all the same wording but make it stand out a little more. Our selling point is the "Same Day Tax Advance up to $6,000"

Lending, Small Loans, Tax Services, Title Loans, Personal Loans

```html
<!DOCTYPE html>
<html lang="en">
<head>
<meta charset="utf-8">
<title>Same Day Tax Advance Flyer</title>
<link rel="stylesheet" href="https://fonts.googleapis.com/css2?family=Poppins:wght@500;600;700;800&family=Oswald:wght@700&display=swap">
<style>
  :root {
    --red: #c61f2b;
    --green: #0f5530;
    --green-soft: #7fb894;
    --ink: #2f2f2f;
    --paper: #ffffff;
    --mist: #ececec;
    --page: #f4f4f4;
  }
  * { margin: 0; padding: 0; box-sizing: border-box; }
  html, body { width: 1200px; height: 2331px; overflow: hidden; background: var(--page); }
  body { position: relative; font-family: 'Poppins', sans-serif; }

  .flyer {
    position: absolute; left: 40px; top: 304px;
    width: 817px; height: 1257px;
    transform: scale(1.371); transform-origin: top left;
    background: radial-gradient(ellipse at 50% 45%, var(--paper) 0%, #f3f3f3 55%, var(--mist) 100%);
    box-shadow: 0 10px 30px rgba(0,0,0,.18);
    overflow: hidden;
  }
  .flyer > * { position: absolute; }

  .brand { top: 120px; left: 0; width: 100%; text-align: center; }
  .brand-name { font-weight: 600; font-size: 40px; color: var(--green); letter-spacing: 1px; line-height: 1; display: inline-flex; align-items: center; gap: 12px; }
  .brand-name::before { content: ""; width: 22px; height: 22px; border-radius: 50%; background: var(--red); }

  .headline-top { top: 212px; left: 0; width: 100%; text-align: center; font-weight: 800; font-size: 118px; line-height: 1; color: var(--red); letter-spacing: -2px; }
  .headline-bottom { top: 310px; left: 0; width: 100%; text-align: center; font-weight: 800; font-size: 92px; line-height: 1; color: var(--ink); letter-spacing: -2px; }

  .upto { top: 450px; left: 73px; width: 52px; height: 145px; background: var(--red); border-radius: 10px; display: flex; align-items: center; justify-content: center; }
  .upto span { transform: rotate(-90deg); color: #fff; font-weight: 800; font-size: 38px; white-space: nowrap; }
  .amount { top: 408px; left: 132px; z-index: 2; font-family: 'Oswald', sans-serif; font-weight: 700; font-size: 196px; line-height: 1; color: var(--green); letter-spacing: -5px; text-shadow: -8px 6px 0 var(--green-soft); white-space: nowrap; }

  .hero-photo { top: 392px; left: 600px; width: 200px; height: 290px; border-radius: 100px 100px 36px 36px; background: linear-gradient(180deg, #c9a27f 0%, #c7a483 45%, #2f4a78 85%, #26385c 100%); }

  .offer-rule { top: 716px; left: 70px; width: 675px; height: 3px; background: var(--green); }
  .offer-tag { top: 690px; left: 150px; width: 505px; height: 50px; border: 3px solid var(--green); border-radius: 10px; background: var(--paper); display: flex; align-items: center; justify-content: center; font-weight: 700; font-size: 27px; color: #111; }
  .offer-main { top: 744px; left: 0; width: 100%; text-align: center; font-weight: 800; font-size: 72px; line-height: 1; color: var(--red); letter-spacing: -1px; }
  .offer-base { top: 818px; left: 70px; width: 675px; height: 3px; background: var(--green); }

  .feature { top: 862px; width: 230px; text-align: center; }
  .feature .badge { width: 88px; height: 88px; margin: 0 auto; border-radius: 50%; background: var(--green); border: 3px solid var(--paper); box-shadow: 0 0 0 2px var(--red); display: flex; align-items: center; justify-content: center; }
  .feature p { margin-top: 14px; font-weight: 500; font-size: 27px; line-height: 28px; color: var(--ink); }
  .feature-1 { left: 49px; } .feature-2 { left: 294px; } .feature-3 { left: 541px; }
  .divider { top: 855px; width: 6px; height: 200px; background: linear-gradient(90deg, rgba(0,0,0,.07), rgba(0,0,0,0)); }
  .divider-1 { left: 290px; } .divider-2 { left: 540px; }

  .contact-rule { top: 1090px; left: 70px; width: 675px; border-top: 2px dashed #cfcfcf; }
  .contact-title { top: 1104px; left: 70px; font-weight: 700; font-size: 31px; color: var(--green); }
  .contact-title em { font-style: normal; color: var(--red); }
  .contact-phone { top: 1144px; left: 70px; display: flex; align-items: center; gap: 12px; font-weight: 700; font-size: 36px; color: #111; }
  .address { top: 1108px; left: 445px; display: flex; gap: 12px; }
  .address p { font-weight: 600; font-size: 21px; line-height: 25px; color: #222; }
</style>
</head>
<body>
<main class="flyer">
  <div class="brand"><span class="brand-name">Crestline Financial Group</span></div>

  <h1 class="headline-top">SAME DAY</h1>
  <h2 class="headline-bottom">TAX ADVANCE</h2>

  <div class="upto"><span>UPTO</span></div>
  <div class="hero-photo" role="img" aria-label="Smiling man sitting cross-legged holding a fan of cash and pointing at the amount"></div>
  <div class="amount">$6000</div>

  <div class="offer-rule"></div>
  <div class="offer-tag">FILE YOUR TAXES AND APPLY FOR</div>
  <div class="offer-main">EASY ADVANCE!</div>
  <div class="offer-base"></div>

  <div class="divider divider-1"></div>
  <div class="divider divider-2"></div>

  <div class="feature feature-1">
    <div class="badge">
      <svg width="56" height="56" viewBox="0 0 56 56" fill="none" stroke="#fff" stroke-width="3" stroke-linecap="round">
        <path d="M10 28a18 18 0 0 1 31-12.5"/><path d="M41 9v7h-7"/>
        <path d="M46 28a18 18 0 0 1-31 12.5"/><path d="M15 47v-7h7"/>
        <text x="28" y="33" fill="#fff" stroke="none" font-family="Poppins, sans-serif" font-weight="700" font-size="13" text-anchor="middle">24/7</text>
      </svg>
    </div>
    <p>Available<br>for 24 hours<br>or less</p>
  </div>

  <div class="feature feature-2">
    <div class="badge">
      <svg width="52" height="52" viewBox="0 0 52 52" fill="none" stroke="#fff" stroke-width="2.5" stroke-linejoin="round">
        <rect x="12" y="8" width="28" height="36" rx="2"/>
        <path d="M18 16h16M18 22h16M18 28h8"/>
        <circle cx="31" cy="32" r="4"/><path d="M24 42c1-5 13-5 14 0"/>
      </svg>
    </div>
    <p>Choose<br>Your Loan<br>Account</p>
  </div>

  <div class="feature feature-3">
    <div class="badge">
      <svg width="56" height="56" viewBox="0 0 56 56" fill="none" stroke="#fff" stroke-width="2.5" stroke-linecap="round">
        <circle cx="32" cy="32" r="13"/><path d="M32 24v8l5 4M29 15h6M32 15v4"/>
        <path d="M6 28h10M9 34h8M12 40h7"/>
      </svg>
    </div>
    <p>Quick and<br>Easy</p>
  </div>

  <div class="contact-rule"></div>
  <div class="contact-title">CONTACT US <em>TODAY</em></div>
  <div class="contact-phone">
    <svg width="32" height="32" viewBox="0 0 32 32"><circle cx="16" cy="16" r="16" fill="var(--red)"/><path d="M11 8l3 4-2 2c1 3 3 5 6 6l2-2 4 3-2 3c-7 0-14-7-14-14z" fill="#fff"/></svg>
    <span>555.0142.0199</span>
  </div>
  <div class="address">
    <svg width="26" height="30" viewBox="0 0 26 30"><path d="M13 1C6.5 1 2 6 2 12c0 8 11 17 11 17s11-9 11-17C24 6 19.5 1 13 1z" fill="var(--red)"/><circle cx="13" cy="12" r="4.5" fill="#fff"/></svg>
    <p>Austin – Elm Crossing<br>4820-2 Elm Crossing Ave<br>Austin, Texas 78702</p>
  </div>
</main>
</body>
</html>
```